Construction business card

I need a new business card, they can connect with my logo, brand.
What we do is residential house , design and build
I like: Navy blue / black
I attached our logo, brand,
and, some idea for business card.

```html
<!DOCTYPE html>
<html lang="en">
<head>
<meta charset="UTF-8">
<title>Ridgeline Homes – Business Card</title>
<link href="https://fonts.googleapis.com/css2?family=Poppins:wght@400;500;700&display=swap" rel="stylesheet">
<style>
  :root {
    --backdrop: #1c1c1d;
    --card: #0b0b0c;
    --card-edge: #222224;
    --gloss: #2a2a2d;
    --blue: #4f7cc9;
    --white: #f4f4f4;
    --rule: #6a6a6e;
  }
  * { margin: 0; padding: 0; box-sizing: border-box; }
  html, body {
    width: 1200px; height: 900px; overflow: hidden;
    background: var(--backdrop);
    font-family: "Poppins", sans-serif;
  }
  .canvas { position: relative; width: 1200px; height: 900px; }
  .card {
    position: absolute; width: 560px; height: 320px;
    background: var(--card);
    border: 1px solid var(--card-edge);
    border-radius: 4px;
    box-shadow: 0 18px 40px rgba(0,0,0,0.55);
  }
  .card--front { left: 60px; top: 90px; display: flex; align-items: center; justify-content: center; }
  .card--back { left: 580px; top: 490px; }

  .brand { display: flex; align-items: center; gap: 14px; }
  .brand__mark { width: 22px; height: 22px; }
  .brand__name { font-weight: 700; letter-spacing: 1px; text-transform: uppercase; }

  .card--front .brand__mark { background: var(--gloss); }
  .card--front .brand__name { color: var(--gloss); font-size: 40px; }

  .back__logo { position: absolute; left: 34px; top: 0; bottom: 0; width: 230px; display: flex; align-items: center; }
  .card--back .brand { gap: 10px; }
  .card--back .brand__mark { width: 16px; height: 16px; background: var(--blue); }
  .card--back .brand__name { color: var(--white); font-size: 22px; }

  .back__divider { position: absolute; left: 282px; top: 56px; width: 1px; height: 208px; background: var(--rule); }

  .contact { position: absolute; left: 304px; top: 62px; color: var(--white); }
  .contact__name { color: var(--blue); font-weight: 700; font-size: 17px; letter-spacing: 1px; text-transform: uppercase; line-height: 1.1; }
  .contact__title { font-size: 13px; font-weight: 500; margin-bottom: 22px; }
  .contact__address { font-size: 12px; line-height: 1.45; margin-bottom: 14px; }
  .contact__list { list-style: none; font-size: 12px; }
  .contact__list li { display: flex; align-items: center; gap: 8px; line-height: 1.7; }
  .contact__icon { width: 12px; height: 12px; flex: none; }
</style>
</head>
<body>
<main class="canvas">
  <section class="card card--front" aria-label="Card front">
    <div class="brand">
      <span class="brand__mark"></span>
      <span class="brand__name">Ridgeline Homes</span>
    </div>
  </section>

  <section class="card card--back" aria-label="Card back">
    <div class="back__logo">
      <div class="brand">
        <span class="brand__mark"></span>
        <span class="brand__name">Ridgeline Homes</span>
      </div>
    </div>
    <div class="back__divider"></div>
    <div class="contact">
      <p class="contact__name">Dalton Reeve</p>
      <p class="contact__title">Founder &amp; CEO</p>
      <p class="contact__address">48 Carrow St,<br>Elmwood, VIC 3190</p>
      <ul class="contact__list">
        <li>
          <svg class="contact__icon" viewBox="0 0 24 24" fill="var(--blue)"><path d="M6.6 10.8a15.1 15.1 0 0 0 6.6 6.6l2.2-2.2c.3-.3.7-.4 1-.2 1.1.4 2.3.6 3.6.6.6 0 1 .4 1 1V20c0 .6-.4 1-1 1A17 17 0 0 1 3 4c0-.6.4-1 1-1h3.5c.6 0 1 .4 1 1 0 1.3.2 2.5.6 3.6.1.3 0 .7-.2 1z"/></svg>
          <span>0400 555 018</span>
        </li>
        <li>
          <svg class="contact__icon" viewBox="0 0 24 24" fill="var(--blue)"><path d="M2 5h20v14H2z M2 5l10 8 10-8" stroke="var(--card)" stroke-width="1.5"/></svg>
          <span>info@ridgelinehomes.com.au</span>
        </li>
        <li>
          <svg class="contact__icon" viewBox="0 0 24 24" fill="none" stroke="var(--blue)" stroke-width="2.4"><circle cx="12" cy="12" r="9.5"/><path d="M2.5 12h19M12 2.5c3 3 3 16 0 19M12 2.5c-3 3-3 16 0 19"/></svg>
          <span>www.ridgelinehomes.com.au</span>
        </li>
      </ul>
    </div>
  </section>
</main>
</body>
</html>
```